"Harbor Builders" is a residential building company and needs a new business card design and may re

We would like a redesign based on the existing logo, and would like to see a new font as well. We are bespoke home builders who build sustainable energy efficient homes.

Industry/Entity Type

Construction

Contact Information for Business Card

Business card size 40mm x 90mm

Colors

Designer to choose colors to be used in the design.

```html
<!DOCTYPE html>
<html lang="en">
<head>
<meta charset="utf-8">
<title>Harbor Builders – Business Card</title>
<link rel="stylesheet" href="https://fonts.googleapis.com/css2?family=Roboto:wght@400;500;700&family=Roboto+Condensed:wght@700&display=swap">
<style>
  :root {
    --backdrop: #5b4a3b;
    --card-white: #f1f1f1;
    --brand-green: #b4c92e;
    --ink: #0b0b0c;
    --text-grey: #4a4a4a;
    --divider: #9a9a9a;
    --white: #ffffff;
  }
  * { margin: 0; padding: 0; box-sizing: border-box; }
  html, body {
    width: 1200px; height: 960px; overflow: hidden;
    background: var(--backdrop);
    font-family: "Roboto", Arial, sans-serif;
  }
  .canvas { position: relative; width: 1200px; height: 960px; }

  .card { position: absolute; width: 600px; height: 343px; overflow: hidden; }

  /* Front */
  .card-front { left: 314px; top: 113px; background: var(--card-white); }
  .card-front .accent-bands { position: absolute; inset: 0; }
  .brand {
    position: absolute; left: 40px; top: 148px;
    display: flex; align-items: center; gap: 12px;
  }
  .brand-square { width: 22px; height: 22px; background: var(--brand-green); }
  .brand-name {
    font-family: "Roboto", Arial, sans-serif; font-weight: 700;
    font-size: 27px; color: var(--ink); letter-spacing: -0.3px;
  }
  .divider {
    position: absolute; left: 296px; top: 72px;
    width: 1px; height: 198px; background: var(--divider);
  }
  .contact { position: absolute; left: 320px; top: 72px; color: var(--text-grey); }
  .contact-name {
    font-family: "Roboto Condensed", "Arial Narrow", sans-serif;
    font-weight: 700; font-size: 22px; color: var(--ink);
    margin-bottom: 10px; letter-spacing: 0.2px;
  }
  .company { font-weight: 500; font-size: 14px; line-height: 18px; color: #3d3d3d; }
  .address, .registration { font-size: 14px; line-height: 18px; }
  .registration { margin-top: 3px; }
  .contact-lines { margin-top: 6px; list-style: none; }
  .contact-lines li {
    display: flex; align-items: center; gap: 9px;
    font-size: 14px; line-height: 19px;
  }
  .contact-lines svg { width: 13px; height: 13px; flex: none; fill: var(--ink); }

  /* Back */
  .card-back { left: 311px; top: 472px; background: var(--brand-green); }
  .back-brand {
    position: absolute; left: 0; right: 0; top: 130px;
    text-align: center; font-weight: 700; font-size: 46px;
    color: var(--white); letter-spacing: -0.5px;
  }
  .back-web {
    position: absolute; left: 0; right: 0; top: 297px;
    text-align: center; font-size: 14px; letter-spacing: 3px; color: var(--white);
  }
</style>
</head>
<body>
<main class="canvas">
  <section class="card card-front" aria-label="Card front">
    <svg class="accent-bands" width="600" height="343" viewBox="0 0 600 343" aria-hidden="true">
      <polygon points="0,0 600,0 0,41" fill="var(--brand-green)"/>
      <polygon points="0,343 600,300 600,343" fill="var(--ink)"/>
    </svg>
    <div class="brand">
      <span class="brand-square"></span>
      <span class="brand-name">harbor builders</span>
    </div>
    <div class="divider"></div>
    <div class="contact">
      <h1 class="contact-name">DANIEL MORROW</h1>
      <p class="company">Harbor Builders Pty Ltd</p>
      <p class="address">PO Box 4120 Northgate<br>LPO Bayside WA 6090</p>
      <p class="registration">Registration 30418<br>ABN: 42 508 339 176</p>
      <ul class="contact-lines">
        <li><svg viewBox="0 0 16 16"><path d="M4 0h8a1 1 0 0 1 1 1v14a1 1 0 0 1-1 1H4a1 1 0 0 1-1-1V1a1 1 0 0 1 1-1zm1 2v10h6V2zm3 11a1 1 0 1 0 0 2 1 1 0 0 0 0-2z"/></svg>0491 572 038</li>
        <li><svg viewBox="0 0 16 16"><path d="M1 3h14v10H1zm1.5 1.5v.3L8 8.6l5.5-3.8v-.3z"/></svg>daniel@harborbuilders.com.au</li>
        <li><svg viewBox="0 0 16 16"><circle cx="8" cy="8" r="7.5"/><path d="M5 3c2 1 1 3 3 3s1 3-1 3-2 2-1 4M11 4c-1 2 1 3 2 3M10 11c1-1 3 0 3 0" stroke="#f1f1f1" stroke-width="1.4" fill="none"/></svg>www.harborbuilders.com.au</li>
      </ul>
    </div>
  </section>

  <section class="card card-back" aria-label="Card back">
    <p class="back-brand">harbor builders</p>
    <p class="back-web">www.harborbuilders.com.au</p>
  </section>
</main>
</body>
</html>
```